All-Natural Head Lice Removal company

I need a business card with my pre-existing logo. We are a new company located in Portland Oregon that goes into peoples homes to help with head lice removal. My products and approach are all- natural and also will be around children.On my current logo we used Teal Bl and the color Green. I am open to new ideas just want it simple and creative

Target Market(s)

my biggest market is families of school aged children

Industry/Entity Type

Business

Contact Information for Business Card

see upload for details from previous business card

Font styles to use
Serif

Colors
33a6d7
9bcb3b
f37122

Requirements
Must have
• Basic information/ logo put into a creative format that is catching to the eye
Nice to have
• creative

```html
<!DOCTYPE html>
<html lang="en">
<head>
<meta charset="utf-8">
<title>Clear Crown – Business Card</title>
<link href="https://fonts.googleapis.com/css2?family=Arvo:wght@400;700&display=swap" rel="stylesheet">
<style>
  :root {
    --bg: #e9e6e1;
    --sky: #33a6d7;
    --sky-light: #8fd3f2;
    --ink: #231f20;
    --charcoal: #2c2a2b;
    --leaf: #9bcb3b;
    --paper: #ffffff;
    --muted: #3a3a3a;
  }
  * { box-sizing: border-box; margin: 0; padding: 0; }
  html, body { width: 1200px; height: 913px; overflow: hidden; }
  body {
    background: var(--bg);
    font-family: "Arvo", Georgia, serif;
    position: relative;
  }
  .card {
    position: absolute;
    width: 540px;
    height: 310px;
    border-radius: 18px;
    overflow: hidden;
    box-shadow: 0 10px 28px rgba(0,0,0,.18);
  }
  .card--front { left: 60px; top: 120px; }
  .card--back { left: 600px; top: 483px; background: var(--paper); }

  .card__art { position: absolute; inset: 0; }

  .tagline {
    position: absolute;
    left: 28px; top: 26px;
    font-size: 13px;
    color: var(--muted);
    white-space: nowrap;
  }

  .brand {
    position: absolute;
    display: flex;
    align-items: center;
    gap: 12px;
  }
  .brand__dot {
    border-radius: 50%;
    background: var(--leaf);
    flex: none;
  }
  .brand__name {
    font-weight: 700;
    color: var(--ink);
    line-height: 1;
  }
  .card--front .brand { left: 30px; top: 170px; }
  .card--front .brand__dot { width: 56px; height: 56px; }
  .card--front .brand__name { font-size: 30px; width: 110px; }

  .card--back .brand { left: 50%; top: 70px; transform: translateX(-50%); }
  .card--back .brand__dot { width: 64px; height: 64px; }
  .card--back .brand__name { font-size: 36px; white-space: nowrap; }

  .contact {
    position: absolute;
    right: 28px; top: 112px;
    text-align: right;
    color: var(--paper);
    white-space: nowrap;
  }
  .contact__name { font-weight: 700; font-size: 17px; letter-spacing: .3px; }
  .contact__role { font-size: 12px; color: var(--sky); margin: 2px 0 14px; }
  .contact__line {
    display: flex;
    justify-content: flex-end;
    align-items: center;
    gap: 8px;
    font-size: 13px;
    line-height: 21px;
  }
  .contact__line svg { width: 12px; height: 12px; flex: none; }

  .back-text {
    position: absolute;
    left: 0; right: 0; top: 190px;
    text-align: center;
    color: var(--ink);
    font-size: 15px;
    line-height: 22px;
  }
  .back-text strong { font-weight: 700; }
</style>
</head>
<body>

  <section class="card card--front" aria-label="Business card front">
    <svg class="card__art" viewBox="0 0 540 310" preserveAspectRatio="none" aria-hidden="true">
      <defs>
        <linearGradient id="skyFill" x1="0" y1="0" x2="0" y2="1">
          <stop offset="0" stop-color="#8fd3f2"/>
          <stop offset="1" stop-color="#33a6d7"/>
        </linearGradient>
      </defs>
      <rect width="540" height="310" fill="url(#skyFill)"/>
      <path d="M398 0 C 328 70, 288 200, 168 310" fill="none" stroke="#ffffff" stroke-width="14"/>
      <path d="M420 0 C 350 70, 310 200, 190 310 L540 310 L540 0 Z" fill="#2c2a2b"/>
      <path d="M420 0 C 350 70, 310 200, 190 310" fill="none" stroke="#33a6d7" stroke-width="3"/>
    </svg>

    <p class="tagline">All Natural In-Home Lice Removal Services</p>

    <div class="brand">
      <span class="brand__dot"></span>
      <span class="brand__name">Clear Crown</span>
    </div>

    <div class="contact">
      <p class="contact__name">MAREN HOLLOWAY</p>
      <p class="contact__role">OWNER</p>
      <p class="contact__line">1-855-555-NITS (6487)
        <svg viewBox="0 0 12 12" aria-hidden="true"><path d="M3 1 L5 3.5 L4 5 Q5 7 7 8 L8.5 7 L11 9 L9.5 11 Q3 10 1 2.5 Z" fill="#33a6d7"/></svg>
      </p>
      <p class="contact__line">maren@clearcrown.com
        <svg viewBox="0 0 12 12" aria-hidden="true"><rect x="1" y="2.5" width="10" height="7" fill="none" stroke="#33a6d7" stroke-width="1.3"/><path d="M1 2.5 L6 6.5 L11 2.5" fill="none" stroke="#33a6d7" stroke-width="1.3"/></svg>
      </p>
      <p class="contact__line">www.clearcrown.com
        <svg viewBox="0 0 12 12" aria-hidden="true"><circle cx="6" cy="6" r="5" fill="none" stroke="#33a6d7" stroke-width="1.2"/><ellipse cx="6" cy="6" rx="2.2" ry="5" fill="none" stroke="#33a6d7" stroke-width="1"/><path d="M1 6 H11" stroke="#33a6d7" stroke-width="1"/></svg>
      </p>
    </div>
  </section>

  <section class="card card--back" aria-label="Business card back">
    <div class="brand">
      <span class="brand__dot"></span>
      <span class="brand__name">Clear Crown</span>
    </div>
    <div class="back-text">
      <p><strong>Try Clear Crown Today and Be Lice Free Tomorrow!</strong></p>
      <p>All Natural In-Home Lice Removal Services</p>
      <p>www.clearcrown.com</p>
    </div>
  </section>

</body>
</html>
```